Business Card Design

We like to use greens as you will see in our logo (but not TOO much green). We are a Dental Clinic in a somewhat eccentric community. We do not like the dated sharp designs which we see many dentists use. We're looking for something bright and fresh while still maintaining the integrity of the profession. Elegance is not necessarily what we are going for... we need for the design to be "mature" but also up-lifting.

See our logo.
Updates

Project Deadline Extended
Reason: We have 5 designs which we like. But we'd like to see a few more before committing to a design.

Project Deadline Extended
Reason: We are awaiting revisions to this project. We are still welcoming designs while we wait to see if designers are able to provide to us the revisions we require in order to proceed with a selection.

Target Market(s)

Younger families - ages late 20's to early 40's

Industry/Entity Type

Business

Contact Information for Business Card

Corwel T. Banfry DDS 2730 W. Halvert Rd. Ste. 7 Royal Oak, MI 48391 (248)555-0174 FX (248)555-0189 info@BrightwellDentalCareMi.com BrigthwellDentalCareMi.com on the back of the card we need an appointment reminder (For____ Date___ Time____) with "If you are unable to keep your appointment, kindly give 48 hours notice" at the bottom. No use of teeth in the design. DOUBLE SIDED DESIGN

Requirements
Should not have
• The use of pictures of teeth

```html
<!DOCTYPE html>
<html lang="en">
<head>
<meta charset="utf-8">
<title>Brightwell Dental Care – Business Card</title>
<link href="https://fonts.googleapis.com/css2?family=PT+Sans:wght@400;700&family=Tinos:ital,wght@0,400;0,700;1,400&display=swap" rel="stylesheet">
<style>
  :root {
    --bg: #5b3a22;
    --card: #ffffff;
    --green-dark: #2a7a12;
    --green-light: #9bd63a;
    --ink: #3a3a3a;
    --rule: #8a8a8a;
  }
  * { box-sizing: border-box; margin: 0; padding: 0; }
  html, body { width: 1200px; height: 492px; overflow: hidden; }
  body { background: var(--bg); position: relative; font-family: "PT Sans", Arial, sans-serif; }

  .card {
    position: absolute;
    top: 96px;
    width: 540px;
    height: 300px;
    background: var(--card);
    overflow: hidden;
    box-shadow: 0 6px 18px rgba(0,0,0,.35);
  }
  .card--front { left: 40px; }
  .card--back { left: 620px; }

  /* Front */
  .front-shape { position: absolute; inset: 0; width: 540px; height: 300px; }
  .brand {
    position: absolute;
    left: 40px;
    top: 118px;
    display: flex;
    align-items: center;
    gap: 10px;
    color: var(--green-dark);
    font-weight: 700;
    font-size: 30px;
    line-height: 1;
  }
  .brand__dot { width: 18px; height: 18px; border-radius: 50%; background: var(--green-light); flex: none; }
  .brand__name small { display: block; font-size: 21px; margin-top: 6px; letter-spacing: .5px; }

  .doctor {
    position: absolute;
    right: 22px;
    top: 26px;
    color: #fff;
    font-weight: 700;
    font-size: 18px;
  }
  .doctor span { font-size: 13px; font-weight: 400; }
  .contact-list {
    position: absolute;
    right: 22px;
    top: 80px;
    list-style: none;
    color: #fff;
    font-size: 12.5px;
    line-height: 20px;
  }
  .contact-list li { display: flex; justify-content: flex-end; align-items: center; gap: 5px; }
  .contact-list li.gap { margin-top: 16px; }
  .contact-list svg { width: 12px; height: 12px; flex: none; }
  .address {
    position: absolute;
    right: 22px;
    top: 214px;
    color: #fff;
    font-size: 12.5px;
    text-align: right;
    line-height: 18px;
  }

  /* Back */
  .back-brand {
    position: absolute;
    left: 30px;
    top: 30px;
    display: flex;
    align-items: center;
    gap: 8px;
    color: var(--green-dark);
    font-weight: 700;
    font-size: 22px;
    line-height: 1;
  }
  .back-brand .brand__dot { width: 13px; height: 13px; }
  .back-brand small { display: block; font-size: 15px; margin-top: 4px; }
  .back-brand__rule { position: absolute; left: 30px; top: 80px; width: 150px; height: 2px; background: var(--green-light); }

  .appt-title {
    position: absolute;
    left: 30px;
    top: 96px;
    font-family: "Tinos", "Times New Roman", serif;
    font-weight: 700;
    font-size: 17px;
    line-height: 20px;
    color: var(--green-dark);
    letter-spacing: .3px;
  }
  .appt-title-rule { position: absolute; left: 236px; top: 110px; width: 150px; border-top: 1px dotted var(--rule); }

  .field { position: absolute; font-size: 15px; line-height: 20px; color: var(--ink); display: flex; align-items: flex-end; gap: 6px; }
  .field__line { border-bottom: 1px dotted var(--rule); height: 15px; }
  .field__line--solid { border-bottom: 1px solid var(--rule); }
  .field--name { left: 30px; top: 124px; }
  .field--time { left: 196px; top: 150px; }
  .field--date { left: 30px; top: 178px; }
  .field--next { left: 30px; top: 212px; }
  .box { position: absolute; width: 92px; height: 22px; border: 1px solid #555; background: #fff; }
  .box--date { left: 300px; top: 176px; }
  .box--next { left: 168px; top: 209px; }

  .days { position: absolute; left: 30px; top: 242px; display: flex; align-items: center; gap: 6px; font-weight: 700; font-size: 14px; line-height: 20px; color: var(--ink); }
  .days .day-box { width: 30px; height: 20px; border: 1px solid #555; margin-right: 8px; }

  .notice {
    position: absolute;
    left: 30px;
    right: 20px;
    bottom: 10px;
    font-family: "Tinos", "Times New Roman", serif;
    font-style: italic;
    font-size: 14.5px;
    line-height: 18px;
    color: #555;
  }
</style>
</head>
<body>

<section class="card card--front" aria-label="Business card front">
  <svg class="front-shape" viewBox="0 0 540 300" aria-hidden="true">
    <path d="M282 0 C 228 110, 246 236, 384 300 L 400 300 C 262 232, 244 110, 294 0 Z" fill="var(--green-light)"/>
    <path d="M300 0 C 250 110, 270 230, 410 300 L 540 300 L 540 0 Z" fill="var(--green-dark)"/>
  </svg>

  <div class="brand">
    <span class="brand__dot"></span>
    <span class="brand__name">Brightwell<small>Dental Care</small></span>
  </div>

  <p class="doctor">Corwel T. Banfry, <span>DDS</span></p>

  <ul class="contact-list">
    <li>
      <svg viewBox="0 0 12 12" aria-hidden="true"><circle cx="6" cy="6" r="5.4" fill="none" stroke="#fff" stroke-width="1"/><path d="M4 3.2 L5 5 L4.6 5.6 Q5.4 7 6.6 7.6 L7.2 7.2 L8.8 8.2 L8 9.2 Q5 8.8 3 4.2 Z" fill="#fff"/></svg>
      (248)555-0174
    </li>
    <li>
      <svg viewBox="0 0 12 12" aria-hidden="true"><rect x="3" y="1.5" width="6" height="3" fill="none" stroke="#fff"/><rect x="1" y="4.5" width="10" height="5" rx="1" fill="#fff"/></svg>
      (248)555-0189
    </li>
    <li class="gap">
      <svg viewBox="0 0 12 12" aria-hidden="true"><rect x="1" y="2.5" width="10" height="7" fill="#fff"/><path d="M1 2.5 L6 6.5 L11 2.5" fill="none" stroke="var(--green-dark)"/></svg>
      info@BrightwellDentalCareMi.com
    </li>
    <li>
      <svg viewBox="0 0 12 12" aria-hidden="true"><circle cx="6" cy="6" r="5" fill="none" stroke="#fff"/><ellipse cx="6" cy="6" rx="2.2" ry="5" fill="none" stroke="#fff"/><path d="M1 6 H11" stroke="#fff"/></svg>
      www.BrigthwellDentalCareMi.com
    </li>
  </ul>

  <p class="address">2730 W. Halvert Rd. Ste.<br>7 Royal Oak, MI 48391</p>
</section>

<section class="card card--back" aria-label="Business card back, appointment reminder">
  <div class="back-brand">
    <span class="brand__dot"></span>
    <span>Brightwell<small>Dental Care</small></span>
  </div>
  <div class="back-brand__rule"></div>

  <h2 class="appt-title">YOUR APPOINTMENT</h2>
  <div class="appt-title-rule"></div>

  <div class="field field--name">Name : <span class="field__line" style="width:300px"></span></div>
  <div class="field field--time">Time : <span class="field__line field__line--solid" style="width:90px"></span>am / pm</div>
  <div class="field field--date">Date : <span class="field__line field__line--solid" style="width:90px"></span></div>
  <div class="box box--date"></div>
  <div class="field field--next">Next Appointment</div>
  <div class="box box--next"></div>

  <div class="days">
    MON <span class="day-box"></span>
    TUE <span class="day-box"></span>
    WED <span class="day-box"></span>
    THU <span class="day-box"></span>
    FRI <span class="day-box"></span>
    SAT <span class="day-box"></span>
  </div>

  <p class="notice">If you are unable to keep your appointment, kindly give 48 hours notice</p>
</section>

</body>
</html>
```